Business Card and Letterhead for Pimlu - modern real estate business

I need a double sided business card design for Pimlu. Please see business card brief here https://files.trelvonadocs.com/sheet/r/7QzTmWbaXLJnoPEd-kRyUgFhHsstbvCe2qfoMxDa_pz/view?mode=shared

Please feel free to design the business cards however you feel best. I am happy to give some creative freedoms and then provide feedback from there.

Please then also create a letterhead to match the business card design

Colors

Designer to choose colors to be used in the design.

Requirements
Must have
• Must be a modern, elegant business card which looks very professional

```html
<!DOCTYPE html>
<html lang="en">
<head>
<meta charset="utf-8">
<title>Pimlu Business Card</title>
<link rel="stylesheet" href="https://fonts.googleapis.com/css2?family=Montserrat:wght@400;500;600;700&display=swap">
<style>
  :root {
    --page-bg: #e9e7e4;
    --card-dark: #2d2d2f;
    --card-darker: #1f1f21;
    --pattern-light: #3c3c3f;
    --brand-red: #e0141e;
    --text-light: #f2f2f2;
    --portrait-top: #3a3a3c;
    --portrait-bottom: #232325;
  }
  * { box-sizing: border-box; margin: 0; padding: 0; }
  html, body { width: 1200px; height: 800px; overflow: hidden; }
  body {
    background: var(--page-bg);
    font-family: "Montserrat", Arial, sans-serif;
    position: relative;
  }
  .card {
    position: absolute;
    top: 235px;
    width: 540px;
    height: 330px;
    border: 2px solid var(--brand-red);
    overflow: hidden;
    box-shadow: 0 10px 24px rgba(0,0,0,0.18);
  }
  /* Back side */
  .card-back {
    left: 40px;
    background: var(--card-darker);
  }
  .back-pattern {
    position: absolute;
    inset: 0;
    background: linear-gradient(135deg, var(--pattern-light) 0%, var(--card-dark) 45%, var(--card-darker) 100%);
  }
  .back-brand {
    position: absolute;
    left: 0; right: 0;
    top: 232px;
    text-align: center;
    color: var(--brand-red);
    font-weight: 700;
    font-size: 24px;
    letter-spacing: 2px;
  }
  /* Front side */
  .card-front {
    left: 620px;
    background: var(--card-dark);
  }
  .front-brand {
    position: absolute;
    left: 30px;
    top: 22px;
    color: var(--brand-red);
    font-weight: 700;
    font-size: 58px;
    letter-spacing: 3px;
    line-height: 1;
  }
  .agent {
    position: absolute;
    left: 34px;
    top: 104px;
    color: var(--text-light);
  }
  .agent-name {
    color: var(--brand-red);
    font-weight: 600;
    font-size: 17px;
    letter-spacing: 1px;
    text-transform: uppercase;
  }
  .agent-title {
    font-size: 13px;
    margin-top: 2px;
  }
  .rule {
    width: 120px;
    height: 1px;
    background: var(--brand-red);
    margin: 10px 0 9px;
  }
  .contact-list { list-style: none; }
  .contact-list li {
    display: flex;
    align-items: center;
    gap: 8px;
    font-size: 13px;
    line-height: 19px;
  }
  .contact-list svg { width: 11px; height: 11px; flex: none; }
  .address { font-size: 13px; line-height: 19px; }
  .portrait {
    position: absolute;
    right: 0;
    bottom: 0;
    width: 250px;
    height: 245px;
    background: linear-gradient(180deg, var(--portrait-top) 0%, var(--portrait-bottom) 100%);
  }
</style>
</head>
<body>
  <section class="card card-back" aria-label="Business card back">
    <div class="back-pattern" role="img" aria-label="Repeating faint brand-name pattern in dark grey tones"></div>
    <div class="back-brand">PIMLU</div>
  </section>

  <section class="card card-front" aria-label="Business card front">
    <div class="front-brand">PIMLU</div>
    <div class="agent">
      <div class="agent-name">Jordan Pell</div>
      <div class="agent-title">Licenced Real Estate Agent</div>
      <div class="rule"></div>
      <ul class="contact-list">
        <li>
          <svg viewBox="0 0 24 24" aria-hidden="true"><path fill="var(--brand-red)" d="M6.6 10.8a15 15 0 0 0 6.6 6.6l2.2-2.2c.3-.3.7-.4 1-.2 1.1.4 2.3.6 3.6.6.6 0 1 .4 1 1V20c0 .6-.4 1-1 1A17 17 0 0 1 3 4c0-.6.4-1 1-1h3.5c.6 0 1 .4 1 1 0 1.3.2 2.5.6 3.6.1.3 0 .7-.2 1z"/></svg>
          0412 384 509
        </li>
        <li>
          <svg viewBox="0 0 24 24" aria-hidden="true"><rect x="2" y="5" width="20" height="14" rx="2" fill="var(--brand-red)"/><path d="M3 6l9 7 9-7" stroke="var(--card-dark)" stroke-width="2" fill="none"/></svg>
          jordan@pimlu.com
        </li>
        <li>
          <svg viewBox="0 0 24 24" aria-hidden="true"><circle cx="12" cy="12" r="10" fill="var(--brand-red)"/><path d="M2 12h20M12 2c3 3 3 17 0 20M12 2c-3 3-3 17 0 20" stroke="var(--card-dark)" stroke-width="1.5" fill="none"/></svg>
          www.pimlu.com
        </li>
      </ul>
      <div class="rule"></div>
      <div class="address">PO Box 1190<br>Larkvale NSW 2614</div>
    </div>
    <div class="portrait" role="img" aria-label="Portrait photo of the agent in a dark suit"></div>
  </section>
</body>
</html>
```